Dentistry Office

We want a new design for a Dentist's office website.

The theme is: "We provide high quality, state-of-the-art, dental care in a comfortable, caring environment."

The site currently has a menu on the left of the page with about 40 items on it. There is a great deal of textual content on each page, plus several illustrations.

We want to do this using CSS, so we need specifications in the CSS for all possible elements. The CSS needs to be named in a logical manner for easy use.

Every dentist on the planet seems to use lots of Flash. We don't want to because it is so distracting. We are looking for an elegant solution targeting 24-55 age group, but not excluding anyone.

The following (from another dentist's site) can give you a taste of what we want to communicate on the site:

"After 20 years of teaching dentists how to refine their technique and many years of writing textbooks, I currently devote my time to my office and the hands-on practice of dentistry. I'd like to welcome you personally to my dental practice, and I invite you to meet my highly experienced team of professionals.

"We have offered complete dental care of the highest quality since 1978. We provide Preventive Services, Tooth Whitening and Cosmetic Dentistry for a beautiful smile, Endodontics (root canal treatment) to treat painful teeth, Sedation Dentistry so you can relax, and Dental Implants to restore what is missing. We offer total care.

"Our approach to your health is simple: We use our education, experience and dedication to provide every patient with superior dental care.

"This passion for excellence is not just a goal, but a standard every member of our team holds.

"We also pride ourselves with our state of the art procedures, training and technology. This includes creating a beautiful smile using techniques that preserve as much of the original tooth as possible.

"Our abilities are renowned throughout the dental profession and I hope if you have any questions you will contact us by an e-mail note, by phone or just by dropping by."

Keep in mind the screen shape and dimensions. Your design needs to work in the normal screen proportions, regardless of how it looks when you post it here. Scrolling is OK, but the first impression needs to work.
Updates

Keep in mind that there will be about 250 words, or more, on each page.

Competitors web sites:

http://www.brindlecovedentist.example/

http://www.brindlecovedentalcare.example/

http://www.grinsbymarlowvaledental.example/

http://www.tenbyfamilydentalcare.example/

http://www.quelmardental.example/

http://www.dovrinadental.example/

We need to compete with these.

Target Market(s)

Generally adults seeking the most experienced and comfortable-to-be-with dentist.

Industry/Entity Type

Training

Requirements
Must have
• Must stand apart from other dentists.
• Must be elegant.
• Must have a horizontal menu structure across all columns, NOT a vertical that requires scrolling, no popout, pop down, etc. menus.
• We are looking for something special.
• Do not waste your time or ours putting up templates and things you have used before.
• Personally, I do not see how someone outside the US can understand the northern California dental market. But you are welcome to try.
Should not have
• Flash or graphics that move
• The look of a template
• Folksy fonts
• Looks like you used it 20 times before

```html
<!DOCTYPE html>
<html lang="en">
<head>
<meta charset="utf-8">
<title>Dental Care — Welcome</title>
<link href="https://fonts.googleapis.com/css2?family=Arimo:wght@400&family=Lusitana:wght@400&family=Parisienne&family=Signika:wght@400&display=swap" rel="stylesheet">
<style>
  :root{
    --header-deep:#17423f;
    --header-mid:#2f6664;
    --header-light:#7fb4b5;
    --nav-bg:#05333f;
    --page-bg:#f3f5f5;
    --menu-yellow:#f2b61a;
    --menu-line:#7a5a08;
    --menu-head:#151515;
    --ink:#111111;
    --heading-blue:#1c5e8c;
    --card-border:#c9cfd2;
    --footer-bg:#043343;
    --white:#ffffff;
    --accent-gold:#f6c232;
  }
  *{box-sizing:border-box;margin:0;padding:0}
  html,body{width:1005px;height:1200px;overflow:hidden;background:var(--page-bg)}
  body{position:relative;font-family:"Arimo",Arial,sans-serif;color:var(--ink)}

  .site-header{position:absolute;left:0;top:0;width:1005px;height:294px;
    background:linear-gradient(180deg,var(--header-deep) 0%,var(--header-mid) 60%,var(--header-light) 100%);overflow:hidden}
  .brand{position:absolute;left:38px;top:56px;font-family:"Lusitana",Georgia,serif;font-size:46px;color:var(--white);line-height:1}
  .brand-sub{position:absolute;left:40px;top:107px;font-family:"Signika",Arial,sans-serif;font-size:12px;color:var(--accent-gold)}
  .tagline{position:absolute;left:34px;top:148px;width:310px;font-family:"Parisienne",cursive;font-size:21px;line-height:29px;color:var(--white)}
  .photo{position:absolute;background:var(--white);padding:8px;box-shadow:0 2px 6px rgba(0,0,0,.35)}
  .photo .fill{width:100%;height:100%}
  .photo-left{left:345px;top:95px;width:135px;height:215px;transform:rotate(-9deg)}
  .photo-left .fill{background:linear-gradient(160deg,#d8dcdf,#b9c2c8)}
  .photo-right{left:845px;top:80px;width:130px;height:230px;transform:rotate(6deg)}
  .photo-right .fill{background:linear-gradient(160deg,#eef1f2,#d9c7b8)}
  .photo-main{left:452px;top:33px;width:410px;height:270px;padding:8px 8px 0}
  .photo-main .fill{background:linear-gradient(135deg,#dfe6e8 0%,#a9c8dc 45%,#e8d3b5 100%)}

  .main-nav{position:absolute;left:0;top:294px;width:1005px;height:42px;background:var(--nav-bg);
    border-bottom:2px dotted #9fb3b8;display:flex;align-items:center;padding-left:20px;
    font-family:"Signika",Arial,sans-serif;font-size:17px;color:var(--white)}
  .main-nav span.sep{margin:0 12px}

  .side-menu{position:absolute;left:15px;top:352px;width:225px;height:713px;background:var(--menu-yellow);border-radius:7px;overflow:hidden}
  .side-menu-title{height:35px;background:var(--menu-head);color:var(--white);font-family:"Signika",Arial,sans-serif;font-size:16px;padding:7px 0 0 23px}
  .side-menu ul{list-style:none;margin-top:17px}
  .side-menu li{height:30px;border-bottom:1px dashed var(--menu-line);font-size:12px;line-height:30px;padding-left:38px;position:relative}
  .side-menu li:last-child{border-bottom:none}
  .side-menu li svg{position:absolute;left:19px;top:10px}

  .content{position:absolute;left:277px;top:360px;width:706px}
  .page-title{font-family:"Lusitana",Georgia,serif;font-weight:400;font-size:28px;height:51px;padding-left:3px;border-bottom:1px dashed #9aa0a3}
  .page-title em{font-style:normal;font-size:36px;color:var(--heading-blue)}
  .feature-photo{position:absolute;left:393px;top:70px;width:313px;height:208px;background:var(--white);padding:8px;box-shadow:0 1px 5px rgba(0,0,0,.35)}
  .feature-photo .fill{width:100%;height:100%;background:linear-gradient(135deg,#e9eef0 0%,#b7c6cc 50%,#d7cfc6 100%)}
  .copy{position:absolute;left:6px;top:76px;font-size:12px;line-height:18px}
  .copy p{margin-bottom:18px}
  .copy .narrow{width:372px}
  .copy .wide{width:690px}

  .promo{position:absolute;top:897px;width:215px}
  .promo h2{font-family:"Lusitana",Georgia,serif;font-weight:400;font-size:20px;color:var(--heading-blue);padding-left:3px;height:42px}
  .promo-card{width:215px;height:126px;border:1px solid var(--card-border);border-radius:7px;background:var(--white);padding:5px;box-shadow:0 1px 3px rgba(0,0,0,.15)}
  .promo-card .fill{position:relative;width:100%;height:100%;border-radius:3px}
  .promo-card .label{position:absolute;left:14px;bottom:10px;font-family:"Lusitana",Georgia,serif;font-size:20px;color:var(--white);text-shadow:0 0 3px #0b3046,0 0 2px #0b3046;display:flex;align-items:center;gap:6px}
  .promo-call{left:283px}
  .promo-call .fill{background:linear-gradient(135deg,#e7ecee,#b8c4ca)}
  .promo-call .label{font-size:29px;left:16px}
  .promo-implants{left:525px}
  .promo-implants .fill{background:linear-gradient(135deg,#f1ece6,#d9c2b2)}
  .promo-dentists{left:767px}
  .promo-dentists .fill{background:linear-gradient(135deg,#eef1f2,#c7d3da)}

  .site-footer{position:absolute;left:0;top:1100px;width:1005px;height:100px;background:var(--footer-bg);border-top:2px dotted #9fb3b8}
  .footer-links{position:absolute;right:31px;top:40px;font-size:11px;color:var(--white);white-space:nowrap}
  .footer-links .sep{margin:0 8px}
</style>
</head>
<body>
  <header class="site-header">
    <div class="brand">Dental Care</div>
    <div class="brand-sub">The Best Dental Care of Northern California</div>
    <p class="tagline">We provide high quality, state-of-the-art, dental care in a comfortable, caring environment.</p>
    <div class="photo photo-left"><div class="fill" role="img" aria-label="Photo of a dentist treating a patient"></div></div>
    <div class="photo photo-right"><div class="fill" role="img" aria-label="Photo of a relaxed patient in the dental chair"></div></div>
    <div class="photo photo-main"><div class="fill" role="img" aria-label="Photo of a smiling hygienist showing a patient how to floss"></div></div>
  </header>

  <nav class="main-nav">
    <span>Home</span><span class="sep">|</span>
    <span>About Us</span><span class="sep">|</span>
    <span>Our Practice</span><span class="sep">|</span>
    <span>Procedures</span><span class="sep">|</span>
    <span>Our Mission</span><span class="sep">|</span>
    <span>Dental Implants</span><span class="sep">|</span>
    <span>FAQs</span><span class="sep">|</span>
    <span>Smile Gallery</span><span class="sep">|</span>
    <span>Contact US</span>
  </nav>

  <aside class="side-menu">
    <div class="side-menu-title">Left Menu</div>
    <ul>
      <li><svg width="10" height="10" viewBox="0 0 10 10"><path d="M2 1l4 4-4 4" fill="none" stroke="#fff" stroke-width="1.6" stroke-dasharray="1.5 1"/></svg>Lorem Ipsum Dolor Sit Amet</li>
      <li><svg width="10" height="10" viewBox="0 0 10 10"><path d="M2 1l4 4-4 4" fill="none" stroke="#fff" stroke-width="1.6" stroke-dasharray="1.5 1"/></svg>Lorem Ipsum Dolor Sit Amet</li>
      <li><svg width="10" height="10" viewBox="0 0 10 10"><path d="M2 1l4 4-4 4" fill="none" stroke="#fff" stroke-width="1.6" stroke-dasharray="1.5 1"/></svg>Lorem Ipsum Dolor Sit Amet</li>
      <li><svg width="10" height="10" viewBox="0 0 10 10"><path d="M2 1l4 4-4 4" fill="none" stroke="#fff" stroke-width="1.6" stroke-dasharray="1.5 1"/></svg>Lorem Ipsum Dolor Sit Amet</li>
      <li><svg width="10" height="10" viewBox="0 0 10 10"><path d="M2 1l4 4-4 4" fill="none" stroke="#fff" stroke-width="1.6" stroke-dasharray="1.5 1"/></svg>Lorem Ipsum Dolor Sit Amet</li>
      <li><svg width="10" height="10" viewBox="0 0 10 10"><path d="M2 1l4 4-4 4" fill="none" stroke="#fff" stroke-width="1.6" stroke-dasharray="1.5 1"/></svg>Lorem Ipsum Dolor Sit Amet</li>
      <li><svg width="10" height="10" viewBox="0 0 10 10"><path d="M2 1l4 4-4 4" fill="none" stroke="#fff" stroke-width="1.6" stroke-dasharray="1.5 1"/></svg>Lorem Ipsum Dolor Sit Amet</li>
      <li><svg width="10" height="10" viewBox="0 0 10 10"><path d="M2 1l4 4-4 4" fill="none" stroke="#fff" stroke-width="1.6" stroke-dasharray="1.5 1"/></svg>Lorem Ipsum Dolor Sit Amet</li>
      <li><svg width="10" height="10" viewBox="0 0 10 10"><path d="M2 1l4 4-4 4" fill="none" stroke="#fff" stroke-width="1.6" stroke-dasharray="1.5 1"/></svg>Lorem Ipsum Dolor Sit Amet</li>
      <li><svg width="10" height="10" viewBox="0 0 10 10"><path d="M2 1l4 4-4 4" fill="none" stroke="#fff" stroke-width="1.6" stroke-dasharray="1.5 1"/></svg>Lorem Ipsum Dolor Sit Amet</li>
      <li><svg width="10" height="10" viewBox="0 0 10 10"><path d="M2 1l4 4-4 4" fill="none" stroke="#fff" stroke-width="1.6" stroke-dasharray="1.5 1"/></svg>Lorem Ipsum Dolor Sit Amet</li>
      <li><svg width="10" height="10" viewBox="0 0 10 10"><path d="M2 1l4 4-4 4" fill="none" stroke="#fff" stroke-width="1.6" stroke-dasharray="1.5 1"/></svg>Lorem Ipsum Dolor Sit Amet</li>
      <li><svg width="10" height="10" viewBox="0 0 10 10"><path d="M2 1l4 4-4 4" fill="none" stroke="#fff" stroke-width="1.6" stroke-dasharray="1.5 1"/></svg>Lorem Ipsum Dolor Sit Amet</li>
      <li><svg width="10" height="10" viewBox="0 0 10 10"><path d="M2 1l4 4-4 4" fill="none" stroke="#fff" stroke-width="1.6" stroke-dasharray="1.5 1"/></svg>Lorem Ipsum Dolor Sit Amet</li>
      <li><svg width="10" height="10" viewBox="0 0 10 10"><path d="M2 1l4 4-4 4" fill="none" stroke="#fff" stroke-width="1.6" stroke-dasharray="1.5 1"/></svg>Lorem Ipsum Dolor Sit Amet</li>
      <li><svg width="10" height="10" viewBox="0 0 10 10"><path d="M2 1l4 4-4 4" fill="none" stroke="#fff" stroke-width="1.6" stroke-dasharray="1.5 1"/></svg>Lorem Ipsum Dolor Sit Amet</li>
      <li><svg width="10" height="10" viewBox="0 0 10 10"><path d="M2 1l4 4-4 4" fill="none" stroke="#fff" stroke-width="1.6" stroke-dasharray="1.5 1"/></svg>Lorem Ipsum Dolor Sit Amet</li>
      <li><svg width="10" height="10" viewBox="0 0 10 10"><path d="M2 1l4 4-4 4" fill="none" stroke="#fff" stroke-width="1.6" stroke-dasharray="1.5 1"/></svg>Lorem Ipsum Dolor Sit Amet</li>
      <li><svg width="10" height="10" viewBox="0 0 10 10"><path d="M2 1l4 4-4 4" fill="none" stroke="#fff" stroke-width="1.6" stroke-dasharray="1.5 1"/></svg>Lorem Ipsum Dolor Sit Amet</li>
      <li><svg width="10" height="10" viewBox="0 0 10 10"><path d="M2 1l4 4-4 4" fill="none" stroke="#fff" stroke-width="1.6" stroke-dasharray="1.5 1"/></svg>Lorem Ipsum Dolor Sit Amet</li>
      <li><svg width="10" height="10" viewBox="0 0 10 10"><path d="M2 1l4 4-4 4" fill="none" stroke="#fff" stroke-width="1.6" stroke-dasharray="1.5 1"/></svg>Lorem Ipsum Dolor Sit Amet</li>
    </ul>
  </aside>

  <main class="content">
    <h1 class="page-title">welcome to <em>Dental Care</em></h1>
    <div class="feature-photo"><div class="fill" role="img" aria-label="Photo of a dentist talking with a patient in the chair"></div></div>
    <div class="copy">
      <p class="narrow">"After 20 years of teaching dentists how to refine their technique and many years of writing textbooks, I currently devote my time to my office and the hands-on practice of dentistry. I'd like to welcome you personally to my dental practice, and I invite you to meet my highly experienced team of professionals.</p>
      <p class="narrow">"We have offered complete dental care of the highest quality since 1978. We provide Preventive Services, Tooth Whitening and Cosmetic Dentistry for a beautiful smile, Endodontics (root canal treatment) to treat painful teeth, Sedation Dentistry so you can relax, and Dental Implants to restore what is missing. We offer total care.</p>
      <p class="wide">"Our approach to your health is simple: We use our education, experience and dedication to provide every patient with superior dental care.</p>
      <p class="wide">"This passion for excellence is not just a goal, but a standard every member of our team holds.</p>
      <p class="wide">"We also pride ourselves with our state of the art procedures, training and technology. This includes creating a beautiful smile using techniques that preserve as much of the original tooth as possible.</p>
      <p class="wide">"Our abilities are renowned throughout the dental profession and I hope if you have any questions you will contact us by an e-mail note, by phone or just by dropping by."</p>
    </div>
  </main>

  <section class="promo promo-call">
    <h2>Call Us</h2>
    <div class="promo-card"><div class="fill" role="img" aria-label="Photo of a woman on the phone"><span class="label">555.014.2290</span></div></div>
  </section>
  <section class="promo promo-implants">
    <h2>Dental Implants</h2>
    <div class="promo-card"><div class="fill" role="img" aria-label="Photo of a dentist holding a dental model"><span class="label">More Information
      <svg width="22" height="22" viewBox="0 0 22 22"><circle cx="11" cy="11" r="10" fill="#3a2a22" stroke="#fff" stroke-width="1.5"/><path d="M6 11h9M11 7l4 4-4 4" fill="none" stroke="#fff" stroke-width="1.8"/></svg></span></div></div>
  </section>
  <section class="promo promo-dentists">
    <h2>Meet The Dentists</h2>
    <div class="promo-card"><div class="fill" role="img" aria-label="Photo of the dental team"><span class="label">View List of Dentists</span></div></div>
  </section>

  <footer class="site-footer">
    <div class="footer-links">© Copyright Dental Care<span class="sep">|</span>All Rights &nbsp;Reserved &nbsp;Home<span class="sep">|</span>About Us<span class="sep">|</span>Our Practice<span class="sep">|</span>Procedures<span class="sep">|</span>Our Mission<span class="sep">|</span>Dental Implants<span class="sep">|</span>FAQs<span class="sep">|</span>Smile Gallery<span class="sep">|</span>Contact Us</div>
  </footer>
</body>
</html>
```